Business Card for a Creative Technology based HR services company

Our company name is Lumo8, and we build large communities of HR (human resource) and finance personnels through our mobile platform, and we conduct lots of on-line and off-line activities to get everyone constantly connected. Behind all these, we will also provide on-site HR and finance contractors to our clients, plus a host of other HR-related services. No process in our company takes more than 5-steps.
Our company slogan: Touching Your Future
Target Market(s)
All human resource (HR) and finance personnels, from new entrants to highly experienced senior professionals.
Industry/Entity Type
Finance
Colors
Designer to choose colors to be used in the design.
Look and feel
Each slider illustrates characteristics of the customer's brand and the style your logo design should communicate.

```html
<!DOCTYPE html>
<html lang="en">
<head>
<meta charset="utf-8">
<title>Lumo8 Business Card</title>
<link href="https://fonts.googleapis.com/css2?family=Exo+2:wght@400;600;800&display=swap" rel="stylesheet">
<style>
  :root {
    --red: #e8141b;
    --navy: #0e2a52;
    --card: #ffffff;
    --ink: #2a2a2a;
    --stage: #2b2b2b;
  }
  * { margin: 0; padding: 0; box-sizing: border-box; }
  html, body { width: 1200px; height: 862px; overflow: hidden; }
  body {
    background: var(--stage);
    font-family: "Exo 2", sans-serif;
    position: relative;
  }
  .card {
    position: absolute;
    top: 100px;
    width: 380px;
    height: 662px;
    background: var(--card);
    overflow: hidden;
  }
  .card--front { left: 190px; }
  .card--back { left: 630px; }
  .card__shapes { position: absolute; inset: 0; }
  .brand-name {
    position: absolute;
    left: 0; right: 0;
    text-align: center;
    font-weight: 800;
    font-size: 76px;
    letter-spacing: -1px;
    color: var(--navy);
  }
  .card--front .brand-name { top: 70px; }
  .card--back .brand-name { top: 110px; }
  .person {
    position: absolute;
    top: 250px;
    left: 0; right: 0;
    text-align: center;
    color: var(--red);
  }
  .person__name { font-size: 30px; font-weight: 600; letter-spacing: 2px; }
  .person__title { font-size: 15px; font-weight: 400; letter-spacing: 2px; margin-top: 2px; }
  .contact {
    position: absolute;
    left: 92px;
    display: flex;
    align-items: center;
    gap: 14px;
    color: var(--ink);
    font-size: 15px;
    line-height: 1.45;
    letter-spacing: 1px;
  }
  .contact--phone { top: 345px; }
  .contact--web { top: 410px; }
  .contact__icon { width: 30px; height: 30px; flex: none; }
  .address {
    position: absolute;
    left: 60px;
    bottom: 44px;
    color: #fff;
    font-size: 17px;
    line-height: 1.5;
    letter-spacing: 1px;
  }
  .back-site {
    position: absolute;
    right: 22px;
    bottom: 26px;
    font-size: 13px;
    letter-spacing: 1px;
    color: var(--ink);
  }
</style>
</head>
<body>
  <section class="card card--front">
    <svg class="card__shapes" width="380" height="662" viewBox="0 0 380 662">
      <path d="M0 0 H46 Q20 30 20 80 V310 Q20 350 0 372 Z" fill="var(--red)"/>
      <path d="M0 510 Q70 500 120 520 Q170 540 230 520 L380 470 V662 H0 Z" fill="var(--navy)"/>
    </svg>
    <div class="brand-name">Lumo8</div>
    <div class="person">
      <div class="person__name">DANIEL REYES</div>
      <div class="person__title">GENERAL MANAGER</div>
    </div>
    <div class="contact contact--phone">
      <svg class="contact__icon" viewBox="0 0 30 30">
        <circle cx="15" cy="15" r="14" fill="var(--red)"/>
        <path d="M10 9 h3 l1 3 -2 1.5 q1.5 3 4.5 4.5 l1.5 -2 3 1 v3 q-1 1 -3 1 q-9 -2 -10 -10 q0 -2 2 -2z" fill="#fff"/>
      </svg>
      <div>014 552 7310<br>014 552 7311</div>
    </div>
    <div class="contact contact--web">
      <svg class="contact__icon" viewBox="0 0 30 30">
        <circle cx="15" cy="15" r="14" fill="var(--red)"/>
        <g fill="none" stroke="#fff" stroke-width="1.4">
          <circle cx="15" cy="15" r="8"/>
          <ellipse cx="15" cy="15" rx="3.5" ry="8"/>
          <path d="M7 15 H23 M8.5 11 H21.5 M8.5 19 H21.5"/>
        </g>
      </svg>
      <div>hello@lumo8mail.com<br>www.lumo8hr.com</div>
    </div>
    <div class="address">42 Harbor Lane,<br>Block C, 2nd floor</div>
  </section>

  <section class="card card--back">
    <div class="brand-name">Lumo8</div>
    <div class="back-site">www.lumo8hr.com</div>
  </section>
</body>
</html>
```